Keystonery Billboard - Financial Services Company (Investments, Tax Planning and Insurance)

Our new office has a billboard directly above the office building. We'd like something eye-catching with a strong Call to Action, with the main part of the billboard being under 7 words if possible. We'd like you to include a way to get ahold of us (either our website keystoneryllc.example or our phone number 302-418-2907. You may also include in small font something to indicate that we've been serving the area since 1980 (the DE area, the tri-state area, the Marlowe Hollow, etc.)

We offer financial planning, tax planning, and insurance, and we help our clients to focus on their goals and happiness by providing everything they need for lifelong wealth under one roof.

Our logos are attached, we use a triangle logo with green and gray. We use the tagline "discover lasting prosperity" but this does not need to be included.

Potential ideas we have seen from other financial companies-
- the concept that the driver spends more time looking at billboards than planning for their retirement
-something along the lines of "everything you need for your finances is in this building right here" planning, investments, taxes, insurance"
-don't spend your time worrying about retirement, let us help you plan for it
-are you working for your money, or is it working for you?
- retirement takes planning, we're here to help
- ready to retire? talk to us
- need investment advice?
- need help investing?
- crossing your fingers isn't a retirement plan. we can help.
- retiring soon? you need help.

Those are just general ideas, please feel free to be creative.

brand colors:
#00b585
#00b185
#000000
#ffffff
#6d6f75
#6d6f75
#6f7074
#021712
#052e24

```html
<!DOCTYPE html>
<html lang="en">
<head>
<meta charset="utf-8">
<title>Keystonery Billboard</title>
<link rel="stylesheet" href="https://fonts.googleapis.com/css2?family=Anton&family=Cormorant+Garamond:wght@500&family=Oswald:wght@500;600&display=swap">
<style>
  :root {
    --board-bg: #fdfbf6;
    --brand-green: #0b8c48;
    --ink: #050807;
    --band-gray: #3b3e40;
    --band-text: #ffffff;
    --mark-gray: #6d6f75;
  }
  * { margin: 0; padding: 0; box-sizing: border-box; }
  html, body { width: 1200px; height: 800px; overflow: hidden; }
  body { background: var(--board-bg); }
  .billboard {
    position: relative;
    width: 1200px;
    height: 800px;
    background: var(--board-bg);
    display: flex;
    flex-direction: column;
    align-items: center;
  }
  .brand {
    margin-top: 120px;
    display: flex;
    align-items: center;
    gap: 14px;
  }
  .brand-square {
    width: 30px;
    height: 30px;
    background: var(--brand-green);
  }
  .brand-name {
    font-family: "Cormorant Garamond", serif;
    font-weight: 500;
    font-size: 58px;
    color: var(--brand-green);
    line-height: 1;
  }
  .headline {
    margin-top: 40px;
    text-align: center;
    font-family: "Anton", sans-serif;
    text-transform: uppercase;
    line-height: 1.08;
    transform: skewX(-6deg);
  }
  .headline-lead {
    display: block;
    font-size: 96px;
    color: var(--brand-green);
    letter-spacing: 1px;
  }
  .headline-action {
    display: block;
    font-size: 118px;
    color: var(--ink);
    letter-spacing: 1px;
  }
  .contact-band {
    position: absolute;
    left: 0;
    right: 0;
    bottom: 0;
    height: 78px;
    background: var(--band-gray);
    color: var(--band-text);
    display: flex;
    align-items: center;
    justify-content: space-between;
    padding: 0 44px;
    font-family: "Oswald", sans-serif;
    font-weight: 500;
  }
  .service-area { font-size: 21px; font-style: italic; }
  .contact-item {
    display: flex;
    align-items: center;
    gap: 10px;
    font-size: 28px;
    font-weight: 600;
    letter-spacing: 0.5px;
  }
  .contact-item svg { width: 26px; height: 26px; }
  .contact-group { display: flex; gap: 48px; }
</style>
</head>
<body>
  <main class="billboard">
    <div class="brand">
      <span class="brand-square"></span>
      <span class="brand-name">Keystonery</span>
    </div>
    <h1 class="headline">
      <span class="headline-lead">Financial Freedom Awaits</span>
      <span class="headline-action">Start Planning Today</span>
    </h1>
    <footer class="contact-band">
      <p class="service-area">Proudly Serving the DE Area, Tri-State, Marlowe Hollow, etc. Since 1980</p>
      <div class="contact-group">
        <span class="contact-item">
          <svg viewBox="0 0 24 24" aria-hidden="true">
            <circle cx="12" cy="12" r="12" fill="#ffffff"/>
            <path d="M8.2 6.5l1.8-.4 1.2 2.9-1.3 1c.6 1.4 1.7 2.5 3.1 3.1l1-1.3 2.9 1.2-.4 1.8c-.2.6-.7 1-1.3 1-4.3-.3-7.7-3.7-8-8 0-.6.4-1.1 1-1.3z" fill="#3b3e40"/>
          </svg>
          302-418-2907
        </span>
        <span class="contact-item">
          <svg viewBox="0 0 24 24" aria-hidden="true">
            <circle cx="12" cy="12" r="11" fill="#ffffff"/>
            <g fill="none" stroke="#3b3e40" stroke-width="1.4">
              <circle cx="12" cy="12" r="7.5"/>
              <ellipse cx="12" cy="12" rx="3.4" ry="7.5"/>
              <path d="M4.5 12h15M5.6 8h12.8M5.6 16h12.8"/>
            </g>
          </svg>
          WWW.KEYSTONERYLLC.EXAMPLE
        </span>
      </div>
    </footer>
  </main>
</body>
</html>
```